Lumbrix Design

Looking for Lumbrix banner and square design:
Lumbrix Banner
W:1600 px H:400 px
Square
120x120

Logo attached.

Description: Data-Driven stock market portfolio management using quantitative analysis.

```html
<!DOCTYPE html>
<html lang="en">
<head>
<meta charset="utf-8">
<title>Lumbrix Banners</title>
<link rel="stylesheet" href="https://fonts.googleapis.com/css2?family=Barlow:wght@400;500;600;700&display=swap">
<style>
  :root {
    --stage: #8f8f8f;
    --light-bg-start: #ffffff;
    --light-bg-end: #dbe6f2;
    --ink-blue: #1a6db3;
    --ink-navy: #12507f;
    --button-blue: #0d5aa6;
    --button-blue-dark: #0b4c8e;
    --deep-blue: #0d3f8f;
    --deep-blue-2: #0a5ea3;
    --white: #ffffff;
    --art-pale: #cfe2f6;
    --art-mid: #5fa9ea;
  }
  * { margin: 0; padding: 0; box-sizing: border-box; }
  html, body {
    width: 1200px; height: 748px; overflow: hidden;
    background: var(--stage);
    font-family: "Barlow", Arial, sans-serif;
  }
  .canvas { position: relative; width: 1200px; height: 748px; }
  .banner {
    position: absolute; left: 71px; width: 1057px; height: 264px;
    box-shadow: 0 4px 14px rgba(0,0,0,0.18);
    overflow: hidden;
  }
  .banner--light {
    top: 75px;
    background: linear-gradient(90deg, var(--light-bg-start) 10%, var(--light-bg-end) 100%);
  }
  .banner--dark {
    top: 408px;
    background:
      radial-gradient(circle at 6% 25%, rgba(90,170,240,0.35), transparent 18%),
      radial-gradient(circle at 62% 75%, rgba(90,170,240,0.25), transparent 22%),
      linear-gradient(90deg, var(--deep-blue) 0%, var(--deep-blue-2) 100%);
  }
  .brand {
    position: absolute; left: 99px; top: 20px;
    display: flex; align-items: center; gap: 9px;
    font-weight: 600; font-size: 26px; letter-spacing: 0.5px;
  }
  .brand__dot { width: 26px; height: 26px; border-radius: 50%; }
  .banner--light .brand { color: var(--ink-blue); }
  .banner--light .brand__dot { background: var(--ink-blue); }
  .banner--dark .brand { color: var(--white); }
  .banner--dark .brand__dot { background: var(--white); }
  .headline {
    position: absolute; left: 98px; top: 86px;
    font-size: 33px; line-height: 36px; font-weight: 400;
    letter-spacing: -0.1px;
  }
  .headline strong { font-weight: 700; }
  .banner--light .headline { color: var(--ink-blue); }
  .banner--light .headline strong { color: var(--ink-navy); }
  .banner--dark .headline { color: var(--white); }
  .cta {
    position: absolute; left: 99px; top: 175px;
    width: 118px; height: 39px; border-radius: 2px;
    display: flex; align-items: center; justify-content: center;
    font-size: 13.5px; font-weight: 500;
  }
  .banner--light .cta {
    background: linear-gradient(90deg, var(--button-blue), var(--button-blue-dark));
    color: var(--white);
  }
  .banner--dark .cta { background: var(--white); color: #1d2a3a; }
  .artwork {
    position: absolute; left: 727px; top: 27px; width: 233px; height: 215px;
    border-radius: 12px;
    background: linear-gradient(135deg, var(--art-pale), var(--art-mid));
    opacity: 0.85;
  }
  .photo {
    position: absolute; left: 733px; top: 29px; width: 232px; height: 205px;
    border-radius: 20px 110px 110px 20px;
    background: linear-gradient(120deg, #dfe7ef 0%, #9fb3c8 55%, #4f6b8c 100%);
  }
</style>
</head>
<body>
<main class="canvas">
  <section class="banner banner--light">
    <div class="brand"><span class="brand__dot"></span>Lumbrix</div>
    <h1 class="headline">Data-Driven stock market <strong>portfolio</strong><br><strong>management using quantitative analysis</strong></h1>
    <div class="cta">Get Started</div>
    <div class="artwork" role="img" aria-label="Isometric illustration of a computer screen with charts, coins and a person analysing data"></div>
  </section>

  <section class="banner banner--dark">
    <div class="brand"><span class="brand__dot"></span>Lumbrix</div>
    <h1 class="headline">Data-Driven stock market <strong>portfolio</strong><br><strong>management using quantitative analysis</strong></h1>
    <div class="cta">Get Started</div>
    <div class="photo" role="img" aria-label="Photo of analysts working in an office, framed in a rounded striped shape"></div>
  </section>
</main>
</body>
</html>
```